Property Finance Company - Orbin Funding Limited

Background: Orbin Funding Group Limited is a private property finance company. Orbin Funding Group has capital to directly fund first mortgage, mezzanine and preferred equity financing. We also acquire performing, sub-performing and distressed debt.

Orbin Fundings management philosophy emphasises expertise, innovation, wisdom, honesty and competitiveness. Orbin Funding are not finance brokers - we provide debt funding to the commercial property and residential development sectors. Our process is built from experience and cumutavely Orbin Fundings Directors have in excess of 60 years wisdom.

The aim of the website will be to increase brand awareness, provide clients with comfort around our level of skill and background on who we are, generate more sales, and provide examples of projects that we have funded.

The website is a new product launch, and we need to use our Orbin Funding logo that has just been designed. We like a dark background, and either black/silver/grey/ jade green, or black/gold/jade green colours.

Our unique advantages are that we have fast turnaround times, we can solve clients funding problems and we know what we are doing. Our target audience will be viewing the website on both desktop and mobile devices.

We would like to have the following pages:

Home
About
Team
Services
Project Experience
Contact

Competitors Website: http://www.tarvolo.example/

We would also like to have the option of video footage in our website, as you can see in our competitors website.

Overall we want a really slick, elegant but modern website that is better than www.tarvolo.example

Target Market(s)

Finance borrowers, property developers, accountants, lawyers, businesspeople, high net worth people

Industry/Entity Type

Finance

Requirements
Must have
• Please see project description
Nice to have
Should not have

```html
<!DOCTYPE html>
<html lang="en">
<head>
<meta charset="utf-8">
<title>Orbin Funding Group</title>
<link href="https://fonts.googleapis.com/css2?family=Crimson+Pro:wght@400;600&family=Open+Sans:wght@400;600&display=swap" rel="stylesheet">
<style>
:root{
  --teal:#3aaa9f;
  --teal-dark:#2f9188;
  --ink:#2b2b2b;
  --body:#555;
  --dark:#2a2a2a;
  --darker:#1e1e1e;
  --footer:#333;
  --line:#e3e3e3;
  --white:#fff;
  --serif:"Crimson Pro",Georgia,serif;
  --sans:"Open Sans",Arial,sans-serif;
}
*{box-sizing:border-box;margin:0;padding:0}
html,body{width:1200px;height:4380px;overflow:hidden}
body{font-family:var(--sans);color:var(--body);background:var(--white);position:relative}
section,header,footer{position:relative;width:1200px;overflow:hidden}
.abs{position:absolute}
.serif{font-family:var(--serif)}
.lorem{font-size:17px;line-height:26px}
.heading{font-family:var(--serif);font-weight:400;font-size:36px;letter-spacing:.5px;text-transform:uppercase;text-align:center;position:absolute;left:0;right:0}
.btn{position:absolute;display:flex;align-items:center;justify-content:center;font-family:var(--serif);font-size:18px;text-transform:uppercase;letter-spacing:.5px}
.ph{position:absolute}

/* hero */
.hero{height:710px;background:linear-gradient(115deg,#5a6066 0%,#7d858c 40%,#3e454b 75%,#2a2f34 100%)}
.hero::after{content:"";position:absolute;inset:0;background:rgba(20,22,25,.35)}
.hero > *{z-index:2}
.brand{left:79px;top:20px;width:160px;text-align:center;color:var(--white)}
.brand .mark{width:46px;height:46px;border:2px solid var(--white);border-radius:50%;margin:0 auto 8px}
.brand .name{font-family:var(--serif);font-size:22px;line-height:22px;letter-spacing:.5px;text-transform:uppercase}
.nav{top:58px;left:470px;display:flex;gap:0;font-size:19px;color:var(--white)}
.nav span{padding:8px 14px;margin-right:6px}
.nav .active{border:1px solid rgba(255,255,255,.6)}
.hero-title{left:82px;top:335px;font-family:var(--serif);font-size:52px;color:var(--white);text-transform:uppercase;font-weight:400}
.hero-text{left:82px;top:412px;width:650px;color:var(--white)}
.btn-ghost{border:2px solid var(--white);color:var(--white)}
.btn-solid{background:var(--white);color:var(--ink)}
.hero-person{left:765px;top:190px;width:350px;height:520px;background:linear-gradient(180deg,#8c8f94,#3d4147);border-radius:170px 170px 0 0}

/* about */
.about{height:584px}
.laptop{left:0;top:93px;width:584px;height:394px}
.about-title{left:581px;top:150px;font-family:var(--serif);font-size:36px;color:var(--teal);text-transform:uppercase}
.about-text{left:581px;top:200px;width:540px}
.btn-teal{border:2px solid var(--teal);color:var(--teal)}

/* services */
.services{height:519px;background:linear-gradient(180deg,#2d2d2d,#232323)}
.services .heading{top:60px;color:var(--white)}
.svc{position:absolute;top:125px;width:225px;height:340px;border:1px solid rgba(255,255,255,.25);text-align:center;color:var(--white)}
.svc .ph{left:10px;top:10px;width:203px;height:180px}
.svc h3{position:absolute;top:204px;left:0;right:0;font-family:var(--serif);font-weight:400;font-size:24px}
.svc p{position:absolute;top:238px;left:12px;right:12px;font-size:15px;line-height:23px;color:#ddd}

/* expertise */
.expertise{height:354px}
.expertise .heading{top:40px;color:var(--teal)}
.exp{position:absolute;top:124px;width:200px;text-align:center}
.exp .ring{width:116px;height:116px;border-radius:50%;margin:0 auto;background:#f1f1f1;display:flex;align-items:center;justify-content:center}
.exp .ring div{width:92px;height:92px;border-radius:50%;background:var(--white);border:2px solid var(--teal);display:flex;align-items:center;justify-content:center}
.exp p{margin-top:20px;font-family:var(--serif);font-size:22px;color:var(--ink)}

/* team */
.team{height:554px;background:var(--teal)}
.team .heading{top:42px;color:var(--white)}
.member{position:absolute;top:140px;width:321px;height:350px}
.member .frame{position:absolute;left:29px;top:-32px;width:263px;height:382px;border:1px solid rgba(255,255,255,.6)}
.member .ph{left:0;top:0;width:321px;height:204px;background:linear-gradient(180deg,#cfd3d6,#7e8a94)}
.member h3{position:absolute;top:232px;left:0;right:0;text-align:center;font-family:var(--serif);font-weight:600;font-size:25px;color:var(--white)}
.member p{position:absolute;top:270px;left:40px;right:40px;text-align:center;font-size:15px;line-height:24px;color:var(--white)}

/* video */
.video{height:316px;background:linear-gradient(100deg,#3a3e43,#24272b 60%,#30343a)}
.video-title{left:0;right:0;top:100px;display:flex;justify-content:center;align-items:center;gap:24px;font-family:var(--serif);font-size:50px;color:var(--white);text-transform:uppercase}
.video-text{left:150px;right:150px;top:195px;text-align:center;color:var(--white);font-size:16px;line-height:28px}

/* testimonials */
.testimonials{height:257px}
.testimonials .heading{top:38px;color:var(--teal)}
.quote{position:absolute;top:100px;width:320px;padding-left:48px}
.quote .qm{position:absolute;left:0;top:-6px;font-family:var(--serif);font-size:60px;line-height:60px;color:var(--teal)}
.quote p{font-size:15px;line-height:24px}
.quote .client{margin-top:4px;font-size:15px;font-weight:600;color:var(--ink)}

/* blog */
.blog{height:391px}
.blog .heading{top:24px;color:var(--teal)}
.post{position:absolute;top:87px;width:470px;height:231px;border:1px solid var(--line);box-shadow:0 2px 6px rgba(0,0,0,.08)}
.post .ph{left:0;top:0;width:211px;height:231px;background:linear-gradient(160deg,#9aa2aa,#4c5560)}
.date{position:absolute;width:60px;height:72px;background:var(--teal);color:var(--white);text-align:center}
.date b{display:block;font-family:var(--serif);font-size:36px;line-height:44px;font-weight:600}
.date span{font-size:14px;font-weight:600}
.post h3{position:absolute;left:236px;top:28px;width:210px;font-family:var(--serif);font-weight:400;font-size:26px;line-height:30px;color:var(--ink)}
.post p{position:absolute;left:236px;top:98px;width:210px;font-size:15px;line-height:24px}

/* cta */
.cta{height:298px;background:var(--teal)}
.cta .heading{top:68px;color:var(--white)}
.cta-text{left:150px;right:150px;top:120px;text-align:center;color:var(--white);font-size:16px;line-height:28px}
.btn-white-line{border:2px solid var(--white);color:var(--white)}

/* footer */
.footer{height:339px;background:var(--footer);color:var(--white)}
.fnav{left:79px;top:38px;display:flex;gap:26px;font-size:16px}
.social{top:27px;display:flex;gap:10px;left:985px}
.social span{width:42px;height:42px;border-radius:50%;background:var(--white);display:block}
.frule{left:0;right:0;top:93px;height:1px;background:#4a4a4a}
.news{left:79px;top:170px;font-size:16px;color:#ddd}
.field{left:79px;top:222px;width:344px;height:45px;border:1px solid #666;background:#2a2a2a;color:#999;font-size:15px;font-style:italic;padding:12px 16px}
.field-btn{left:423px;top:222px;width:70px;height:45px;background:var(--white);display:flex;align-items:center;justify-content:center}
.flogo{left:955px;top:120px;width:180px;text-align:center;color:#8a8a8a}
.flogo .mark{width:70px;height:70px;border:2px solid #8a8a8a;border-radius:50%;margin:0 auto 12px}
.flogo .name{font-family:var(--serif);font-size:30px;line-height:32px;text-transform:uppercase}
.copy{height:58px;background:var(--darker);color:#ccc;font-size:15px;display:flex;align-items:center;justify-content:center}
</style>
</head>
<body>

<header class="hero">
  <div class="abs brand"><div class="mark"></div><div class="name">Orbin Funding<br>Group</div></div>
  <nav class="abs nav"><span class="active">Home</span><span>About</span><span>Team</span><span>Services</span><span>Project Experience</span><span>Contact</span></nav>
  <h1 class="abs hero-title">Orbin Funding Group</h1>
  <p class="abs hero-text lorem">Lorem ipsum dolor sit amet, consectetur adipiscing elit. Nam tempor faucibus ante, eget vulputate libero pharetra eu. Nulla at felis eros. Sed ut metus justo.</p>
  <div class="btn btn-ghost" style="left:79px;top:485px;width:172px;height:48px">Read More</div>
  <div class="btn btn-solid" style="left:266px;top:485px;width:178px;height:48px">Contact Us</div>
  <div class="ph hero-person" role="img" aria-label="Portrait of a businessman in a suit with arms crossed"></div>
</header>

<section class="about">
  <div class="ph laptop" role="img" aria-label="Laptop showing a market trend line chart" style="background:linear-gradient(180deg,#f4f6fa 0%,#dfe8f5 70%,#3a3f46 70%,#2a2e33 100%)"></div>
  <h2 class="abs about-title">About&nbsp; Orbin Funding Group</h2>
  <p class="abs about-text lorem">Lorem ipsum dolor sit amet, consectetur adipiscing elit. Nam tempor faucibus ante, eget vulputate libero pharetra eu. Nulla at felis eros. Sed ut metus justo. Suspendisse vestibulum dui at magna rutrum vestibulum. Vestibulum ante ipsum primis in faucibus orci luctus et ultrices posuere cubilia Curae; Nullam eget blandit augue. Sed tempus sapien purus, ac sollicitudin sem porttitor a.</p>
  <div class="btn btn-teal" style="left:581px;top:370px;width:172px;height:48px">Read More</div>
</section>

<section class="services">
  <h2 class="heading">Our Best Services</h2>
  <div class="svc" style="left:85px"><div class="ph" role="img" aria-label="Stacks of coins with a hand" style="background:linear-gradient(160deg,#d9d2c2,#8a7a5c)"></div><h3>Debt funding</h3><p>Lorem ipsum dolor sit amet, consectetur adipiscing elit.</p></div>
  <div class="svc" style="left:350px"><div class="ph" role="img" aria-label="Financial charts on a desk" style="background:linear-gradient(160deg,#e3e8ee,#5b7086)"></div><h3>Mezzanine</h3><p>Lorem ipsum dolor sit amet, consectetur adipiscing elit.</p></div>
  <div class="svc" style="left:619px"><div class="ph" role="img" aria-label="Business handshake" style="background:linear-gradient(160deg,#cfd5db,#5d6770)"></div><h3>Equity financing</h3><p>Lorem ipsum dolor sit amet, consectetur adipiscing elit.</p></div>
  <div class="svc" style="left:885px"><div class="ph" role="img" aria-label="Stock market screen with a pen" style="background:linear-gradient(160deg,#3b5a86,#1b2b46)"></div><h3>Perdorming</h3><p>Lorem ipsum dolor sit amet, consectetur adipiscing elit.</p></div>
</section>

<section class="expertise">
  <h2 class="heading">Expertise</h2>
  <div class="exp" style="left:96px"><div class="ring"><div>
    <svg width="44" height="44" viewBox="0 0 44 44" fill="none" stroke="#333" stroke-width="2"><path d="M22 10a9 9 0 0 0-5 16.5V31h10v-4.5A9 9 0 0 0 22 10z"/><path d="M18 35h8M22 4v3M9 9l2 2M35 9l-2 2M5 20h3M36 20h3"/></svg>
  </div></div><p>Innovation</p></div>
  <div class="exp" style="left:364px"><div class="ring"><div>
    <svg width="44" height="44" viewBox="0 0 44 44" fill="none" stroke="#333" stroke-width="2"><circle cx="22" cy="18" r="9"/><path d="M18 30h8M19 35h6M22 14v8M18 18h8"/></svg>
  </div></div><p>Wisdom</p></div>
  <div class="exp" style="left:633px"><div class="ring"><div>
    <svg width="48" height="44" viewBox="0 0 48 44" fill="#333"><path d="M4 16l10-4 8 4 8-4 10 4 4 8-6 2-10 8-6-4-6 4-10-10z"/></svg>
  </div></div><p>Honesty</p></div>
  <div class="exp" style="left:902px"><div class="ring"><div>
    <svg width="44" height="44" viewBox="0 0 44 44" fill="none" stroke="#333" stroke-width="2.5"><path d="M6 36h32M8 30l10-10 7 6 12-13"/><path d="M30 12h7v7"/></svg>
  </div></div><p>Competitivenes</p></div>
</section>

<section class="team">
  <h2 class="heading">Our Team</h2>
  <div class="member" style="left:79px"><div class="frame"></div><div class="ph" role="img" aria-label="Portrait of team member Aria Mendel"></div><h3>Aria Mendel</h3><p>Administrator and Business Development, Partner</p></div>
  <div class="member" style="left:438px"><div class="frame"></div><div class="ph" role="img" aria-label="Portrait of team member Farid Malone"></div><h3>Farid Malone</h3><p>Senior Financial Advisor, Partner</p></div>
  <div class="member" style="left:800px"><div class="frame"></div><div class="ph" role="img" aria-label="Portrait of team member Ines Norwood"></div><h3>Ines Norwood</h3><p>Advertising and Marketing Manager</p></div>
</section>

<section class="video" role="img" aria-label="Dark photo of a business meeting behind the video call-out">
  <div class="abs video-title"><span>Watch</span>
    <svg width="64" height="64" viewBox="0 0 64 64"><circle cx="32" cy="32" r="29" fill="none" stroke="#fff" stroke-width="4"/><path d="M26 19l19 13-19 13z" fill="#fff"/></svg>
  <span>Our Video</span></div>
  <p class="abs video-text">Lorem ipsum dolor sit amet, consectetur adipiscing elit. Nam tempor faucibus ante, eget vulputate libero pharetra eu. Nulla at felis eros. Sed ut metus justo. Suspendisse vestibulum dui at magna rutrum vestibulum.</p>
</section>

<section class="testimonials">
  <h2 class="heading">Testimonials</h2>
  <div class="quote" style="left:79px"><span class="qm">&ldquo;</span><p>Lorem ipsum dolor sit amet, consect adipiscing elit. Nam tempor faucibus ante, eget vulputate libero pharetra.</p><p class="client">- Client Name</p></div>
  <div class="quote" style="left:432px"><span class="qm">&ldquo;</span><p>Lorem ipsum dolor sit amet, consect adipiscing elit. Nam tempor faucibus ante, eget vulputate libero pharetra.</p><p class="client">- Client Name</p></div>
  <div class="quote" style="left:791px"><span class="qm">&ldquo;</span><p>Lorem ipsum dolor sit amet, consect adipiscing elit. Nam tempor faucibus ante, eget vulputate libero pharetra.</p><p class="client">- Client Name</p></div>
</section>

<section class="blog">
  <h2 class="heading">Latest Blog</h2>
  <article class="post" style="left:96px">
    <div class="ph" role="img" aria-label="Business team celebrating in an office"></div>
    <div class="date" style="left:151px;top:30px"><b>29</b><span>APR</span></div>
    <h3>Lorem Ipsum is simply dummy text.</h3>
    <p>Lorem Ipsum is simply dummy text of the printing and typesetting industry. Lorem Ipsum has been the industry's standard dummy.</p>
  </article>
  <article class="post" style="left:634px">
    <div class="ph" role="img" aria-label="Businessman working on a tablet"></div>
    <div class="date" style="left:151px;top:125px"><b>29</b><span>APR</span></div>
    <h3>Lorem Ipsum is simply dummy text.</h3>
    <p>Lorem Ipsum is simply dummy text of the printing and typesetting industry. Lorem Ipsum has been the industry's standard dummy.</p>
  </article>
</section>

<section class="cta">
  <h2 class="heading">How can our experts help you?</h2>
  <p class="abs cta-text">Lorem ipsum dolor sit amet, consectetur adipiscing elit. Nam tempor faucibus ante, eget vulputate libero pharetra eu. Nulla at felis eros. Sed ut metus justo. Suspendisse vestibulum dui at magna rutrum vestibulum.</p>
  <div class="btn btn-white-line" style="left:511px;top:190px;width:178px;height:47px">Join Now</div>
</section>

<footer class="footer">
  <nav class="abs fnav"><span>Home</span><span>About</span><span>Team</span><span>Services</span><span>Project Experience</span><span>Contact</span></nav>
  <div class="abs social"><span></span><span></span><span></span></div>
  <div class="abs frule"></div>
  <p class="abs news">Get valuable content every day. Subscribe to our newsletter.</p>
  <div class="abs field">Enter Your Email</div>
  <div class="abs field-btn"><svg width="30" height="22" viewBox="0 0 30 22" fill="none" stroke="#3aaa9f" stroke-width="2"><rect x="1" y="1" width="28" height="20"/><path d="M1 1l14 11L29 1"/></svg></div>
  <div class="abs flogo"><div class="mark"></div><div class="name">Orbin Funding<br>Group</div></div>
</footer>
<div class="copy">&copy;ORBIN FUNDING GROUP - 2017. All Rights Reserved.</div>

</body>
</html>
```